Etiketten-Design für nachhaltige Rasur- & Pflegeprodukte
> Wir suchen Verpackung und Etiketten für eine Marke für nachhaltige Rasur- & Pflegeprodukte.
Habedere liebe Designer,
„Habedere“ sagt man bei uns in Bayern, es bedeutet Hallo oder auf Wiedersehen, je nach Gelegenheit. In diesem Fall: Hallo.
Vielleicht kennst du uns schon, wir sind greenpines, wir betreiben einen kleinen Shop für Bartpflege & Rasur unter greenpines-shop.de und wir versuchen uns nun an einem neuen Thema: nachhaltige Rasur- & Pflegeprodukte für Frauen.
Das machen wir unter dem Namen „Sanft“.
Weil die Frage schon oft aufkam: Jawohl, wir haben uns dafür die Beine und die Achseln mit einem Rasierhobel rasiert.
> Zielgruppe.
Wir arbeiten an einer neuen Pflegelinie für Frauen, die sich vorwiegend mit der Rasur und den dazugehörigen Pflegeprodukten beschäftigt. Die Zielgruppe sind vor allem online-affine Frauen aus Deutschland, Österreich und der Schweiz, aber sicher auch europaweit im Alter von 21-45.
> Aufgabenstellung.
Wir sind auf der Suche nach einem Konzept für unsere Produktverpackungen bzw. Etiketten. Bei den Pflegeprodukten verzichten wir bewusst auf eine Umverpackung.
Konkret geplant sind ein Rasierhobel, dafür haben wir eine schöne Umverpackung. Außerdem starten wir mit Rasieröl, Rasierseife und einem After Shave Balsam. Es werden später noch andere Artikel dazukommen, eine Deocreme zum Beispiel.
Rasieröl, Rasiercreme und After Shave Balsam duften nach Orangen, es werden zwei oder drei weitere Duftrichtungen folgen, die eine wird beispielsweise nach Beeren duften, die andere nach Pfirsich und Mango – bitte beachte das bei der Erstellung des Konzeptes, die Unterschiede sollten später auf den ersten Blick erkennbar sein.
Zurück zum Thema Orange: Wir würden den Duft als leicht herben Zitrusduft bezeichnen.
> Die Maße.
• Umverpackung Rasierhobel, weißer Karton (165x90x40mm)
• Rasieröl 30ml (Etikett: 100x46mm)
• Rasiercreme 60ml (Etikett: 156x32mm)
• After Shave Balsam 60ml (Etikett: 156x32mm)
> Zwingend erforderliche Angaben.
Da es sich um Kosmetikprodukte handelt, sind einige Angaben auf dem Label zwingend erforderlich, beispielhaft sollen die folgenden Infos als Platzhalter dienen.
• Hergestellt für Friedrich Lautner e.K. von greenpines, Lindenhofweg 7, 83109 Kolbermoor
• Ingredients: Aqua, Stearic Acid, Cocos Nucifera oil, Glycerin, Potassium Hydroxide, Litsea Cubeba oil, (and) Citrus Sinensis Peel oil, Orbignya Oleifera oil, Sodium Hydroxide, Macadamia ternifolia oil, Talc, Kaolin, Citric Acid, Simmondsia chinensis oil, Maris sal, C.I. 77892 (and) Rad Clay, Citral, Limonene, Linalool, Geraniol
• Platz für einen Barcode
• Rasieröl sind 30ml / 1.01 FL.OZ. ODER Creme & Balsam jeweils 60ml / 2.03 FL. OZ.
Wir haben ein Bild der aktuellen Gefäße beigefügt, es kann aber durchaus sein, dass wir uns noch umen..

```html
<!DOCTYPE html>
<html lang="de">
<head>
<meta charset="utf-8">
<title>Sanft – Rasieröl Etikett und Rasierhobel Verpackung</title>
<link rel="stylesheet" href="https://fonts.googleapis.com/css2?family=Playfair+Display:wght@900&family=Courier+Prime&family=Dancing+Script:wght@400&display=swap">
<style>
  :root {
    --backdrop: #dedede;
    --paper: #f3f3f1;
    --carton: #f2f1ec;
    --sage: #8aa9a1;
    --navy: #27304d;
    --orange: #e07a1c;
    --cream: #f7f6f1;
  }
  * { box-sizing: border-box; margin: 0; padding: 0; }
  html, body { width: 1200px; height: 900px; overflow: hidden; }
  body {
    background: var(--backdrop);
    position: relative;
    font-family: "Courier Prime", monospace;
  }

  /* shared pieces */
  .brand-disc {
    position: absolute;
    border-radius: 50%;
    background: var(--sage);
    display: flex;
    align-items: center;
    justify-content: center;
  }
  .brand-name {
    font-family: "Courier Prime", monospace;
    color: var(--cream);
    letter-spacing: 0.04em;
  }
  .band {
    position: absolute;
    left: 0; right: 0; bottom: 0;
  }
  .band-edge { position: absolute; left: 0; top: -12px; width: 100%; height: 14px; display: block; }
  .band-fill { position: absolute; inset: 0; background: var(--sage); }
  .band-content {
    position: relative;
    text-align: center;
  }
  .product-title {
    font-family: "Playfair Display", serif;
    font-weight: 900;
    color: var(--navy);
  }
  .origin-note {
    font-family: "Dancing Script", cursive;
    color: var(--cream);
  }
  .detail-line {
    font-family: "Courier Prime", monospace;
    color: var(--navy);
  }

  /* oil label */
  .oil-label {
    position: absolute;
    left: 170px; top: 230px;
    width: 320px; height: 440px;
    background: var(--paper);
    box-shadow: 0 2px 10px rgba(0,0,0,0.08);
    overflow: hidden;
  }
  .oil-label .brand-disc { width: 150px; height: 150px; left: 85px; top: 70px; }
  .oil-label .brand-name { font-size: 30px; }
  .oil-label .band { height: 170px; }
  .oil-label .band-content { padding-top: 24px; }
  .oil-label .product-title { font-size: 28px; line-height: 1.1; }
  .oil-label .scent-name { color: var(--orange); font-size: 18px; margin-top: 4px; }
  .oil-label .origin-note { font-size: 20px; margin-top: 6px; }
  .oil-label .detail-line.volume { font-size: 11px; margin-top: 2px; }
  .blossom-art {
    position: absolute;
    right: 8px; bottom: 8px;
    width: 52px; height: 52px;
    border-radius: 50%;
    background: radial-gradient(circle, rgba(224,122,28,0.22), rgba(224,122,28,0));
  }

  /* razor box front */
  .razor-box {
    position: absolute;
    left: 650px; top: 130px;
    width: 340px; height: 620px;
    background: var(--carton);
    box-shadow: 0 3px 14px rgba(0,0,0,0.10);
    overflow: hidden;
  }
  .razor-box .brand-disc { width: 200px; height: 200px; left: 70px; top: 110px; }
  .razor-box .brand-name { font-size: 40px; }
  .razor-box .band { height: 290px; }
  .razor-box .band-content { padding-top: 44px; }
  .razor-box .product-title { font-size: 38px; }
  .razor-box .origin-note { font-size: 24px; margin-top: 10px; }
  .razor-box .detail-line { font-size: 13px; margin-top: 2px; }
</style>
</head>
<body>

  <section class="oil-label" aria-label="Etikett Rasieröl">
    <div class="brand-disc"><span class="brand-name">Sanft</span></div>
    <div class="band">
      <svg class="band-edge" viewBox="0 0 320 14" preserveAspectRatio="none">
        <path fill="#8aa9a1" d="M0 14 L0 6 L14 4 L26 7 L40 3 L58 6 L72 2 L90 5 L108 3 L124 7 L142 4 L160 6 L178 2 L196 5 L214 3 L230 6 L248 2 L266 5 L284 3 L300 6 L320 4 L320 14 Z"/>
      </svg>
      <div class="band-fill"></div>
      <div class="blossom-art" role="img" aria-label="Feine Illustration einer Orangenblüte"></div>
      <div class="band-content">
        <h1 class="product-title">Rasieröl</h1>
        <p class="detail-line scent-name">Orange Blossom</p>
        <p class="origin-note">handmade in germany</p>
        <p class="detail-line volume">30ml / 1.01 FL.OZ</p>
      </div>
    </div>
  </section>

  <section class="razor-box" aria-label="Verpackung Rasierhobel">
    <div class="brand-disc"><span class="brand-name">Sanft</span></div>
    <div class="band">
      <svg class="band-edge" viewBox="0 0 340 14" preserveAspectRatio="none">
        <path fill="#8aa9a1" d="M0 14 L0 5 L16 3 L30 7 L46 4 L62 6 L80 2 L98 6 L116 3 L134 7 L150 4 L168 6 L186 2 L204 5 L222 3 L240 7 L258 4 L276 6 L294 2 L312 5 L326 3 L340 6 L340 14 Z"/>
      </svg>
      <div class="band-fill"></div>
      <div class="band-content">
        <h2 class="product-title">Rasierhobel</h2>
        <p class="origin-note">produced in germany</p>
        <p class="detail-line">Rasierhobel + 2 Klingen</p>
      </div>
    </div>
  </section>

</body>
</html>
```